RW Framewell Inc Business cards

We need business cards using our existing logo but slightly modified. Right now the logo says RW Loadbearing Masonry. We want to keep the RW part of the design, but replace the Structural Concrete portion with "FRAMEWELL". Please see the attached file.
Ideally this would be a blank template so we can add Different Names, titles, and phone numbers later.
On the one side we want only the logo and on the other side the detail. I'm attaching an example for you to see.
Please reach out with any other questions. Our address and other details will be given out once we find a design we like.

Target Market(s)

Construction Industry

```html
<!DOCTYPE html>
<html lang="en">
<head>
<meta charset="utf-8">
<title>RW Framewell Inc — Business Cards</title>
<link href="https://fonts.googleapis.com/css2?family=Roboto:wght@400;500&display=swap" rel="stylesheet">
<style>
  :root {
    --brand-blue: #1f75c0;
    --ink-grey: #6e6e70;
    --ink-dark: #3b3b3d;
    --paper: #ffffff;
    --backdrop: #e6e7ea;
  }
  * { box-sizing: border-box; margin: 0; padding: 0; }
  html, body {
    width: 1200px; height: 913px; overflow: hidden;
    background: var(--backdrop);
    font-family: "Roboto", Arial, sans-serif;
  }
  .canvas { position: relative; width: 1200px; height: 913px; }

  .card {
    position: absolute;
    width: 640px; height: 366px;
    border-radius: 4px;
    box-shadow: 0 6px 18px rgba(0,0,0,.15);
    overflow: hidden;
  }

  /* Logo side */
  .card--front { left: 170px; top: 62px; background: var(--brand-blue); color: var(--paper); }
  .card--front .wordmark {
    position: absolute; left: 0; right: 0; top: 138px;
    display: flex; justify-content: center; align-items: center; gap: 16px;
  }
  .wordmark { white-space: nowrap; }
  .wordmark__square { width: 22px; height: 22px; background: currentColor; flex: none; }
  .wordmark__name { font-size: 46px; font-weight: 500; letter-spacing: 3px; }
  .card--front .front-url {
    position: absolute; left: 0; right: 0; top: 262px;
    text-align: center; font-size: 17px; letter-spacing: .5px;
  }

  /* Detail side */
  .card--back { left: 390px; top: 486px; background: var(--paper); }
  .card--back .wordmark {
    position: absolute; left: 36px; top: 132px; width: 260px;
    display: flex; align-items: center; gap: 10px;
    color: var(--brand-blue);
  }
  .card--back .wordmark__square { width: 14px; height: 14px; }
  .card--back .wordmark__name { font-size: 27px; letter-spacing: 1.5px; }
  .divider {
    position: absolute; left: 322px; top: 58px;
    width: 2px; height: 184px; background: var(--brand-blue);
  }
  .details { position: absolute; left: 350px; top: 62px; }
  .details__name {
    color: var(--brand-blue); font-size: 25px; font-weight: 500; letter-spacing: .5px;
  }
  .details__title {
    color: var(--ink-grey); font-size: 14px; letter-spacing: 1px; margin-top: 4px;
  }
  .contact-list { list-style: none; margin-top: 20px; }
  .contact-list li {
    display: flex; align-items: center; gap: 12px;
    color: var(--ink-dark); font-size: 18px; line-height: 30px;
  }
  .contact-list svg { width: 16px; height: 16px; fill: var(--brand-blue); flex: none; }
  .address-band {
    position: absolute; left: 0; right: 0; bottom: 28px; height: 40px;
    background: var(--brand-blue); color: var(--paper);
    display: flex; align-items: center; justify-content: center;
    font-size: 15px; letter-spacing: .3px;
  }
</style>
</head>
<body>
<main class="canvas">

  <section class="card card--front" aria-label="Card logo side">
    <div class="wordmark">
      <span class="wordmark__square"></span>
      <span class="wordmark__name">RW FRAMEWELL</span>
    </div>
    <p class="front-url">www.rwframewell.com</p>
  </section>

  <section class="card card--back" aria-label="Card detail side">
    <div class="wordmark">
      <span class="wordmark__square"></span>
      <span class="wordmark__name">RW FRAMEWELL</span>
    </div>
    <div class="divider"></div>
    <div class="details">
      <p class="details__name">DANIEL WHITFORD</p>
      <p class="details__title">DIRECTOR</p>
      <ul class="contact-list">
        <li>
          <svg viewBox="0 0 24 24" aria-hidden="true"><path d="M6.6 10.8a15 15 0 0 0 6.6 6.6l2.2-2.2c.3-.3.7-.4 1-.2 1.1.4 2.3.6 3.6.6.6 0 1 .4 1 1V20c0 .6-.4 1-1 1C10.6 21 3 13.4 3 4c0-.6.4-1 1-1h3.5c.6 0 1 .4 1 1 0 1.3.2 2.5.6 3.6.1.3 0 .7-.2 1z"/></svg>
          0987654321
        </li>
        <li>
          <svg viewBox="0 0 24 24" aria-hidden="true"><path d="M2 5h20v14H2zm2 2v.5l8 5 8-5V7zm0 2.8V17h16V9.8l-8 5z"/></svg>
          info@rwframewell.com
        </li>
        <li>
          <svg viewBox="0 0 24 24" aria-hidden="true"><path d="M12 2a10 10 0 1 0 0 20 10 10 0 0 0 0-20zm6.9 6h-3a15 15 0 0 0-1.3-3.9A8 8 0 0 1 18.9 8zM12 4c.8 1.2 1.5 2.5 1.9 4h-3.8c.4-1.5 1.1-2.8 1.9-4zM4.3 14a8 8 0 0 1 0-4h3.4a16 16 0 0 0 0 4zm.8 2h3a15 15 0 0 0 1.3 3.9A8 8 0 0 1 5.1 16zm3-8h-3a8 8 0 0 1 4.3-3.9C8.8 5.3 8.4 6.6 8.1 8zM12 20c-.8-1.2-1.5-2.5-1.9-4h3.8c-.4 1.5-1.1 2.8-1.9 4zm2.3-6H9.7a14 14 0 0 1 0-4h4.6a14 14 0 0 1 0 4zm.3 5.9c.6-1.2 1-2.5 1.3-3.9h3a8 8 0 0 1-4.3 3.9zm1.7-5.9a16 16 0 0 0 0-4h3.4a8 8 0 0 1 0 4z"/></svg>
          www.rwframewell.com
        </li>
      </ul>
    </div>
    <div class="address-band">48 Harlow Road, Eastfield, NW4 (Eastfield Station Exit B)</div>
  </section>

</main>
</body>
</html>
```